Sophisticated, clean website reflecting my feminine, playful side to sell my abstract art,

I need a website no more than 3 pages to showcase my paintings, a little about me and some contact info. I do abstracts so looking for something a little edgy, yet feminine and current.
Updates

Hi there, These are some artists websites that I Iike: Marnelvoss.com (I like how airy it is) peterwallombry.com garethpolvens.com (I like how it scrolls) I'll need a place for a photo ( a headshot-i do not have it yet so I'll need to be able to upload that later) as well as an area for my bio. Also, it's important that I will be able to upload any new photos and descriptions easily so it should be user friendly. Lastly, I like in a sunny place so would like to have this seem upbeat and playful as that is how i like to paint. thanks-I'm trying to upload my photos now -

Target Market(s)

ppl ages 35-70 who want large scale art for their homes

Industry/Entity Type

art

Coding

Coded - Design and coding required

Number of Pages Required

3 page

Colors

Designer to choose colors to be used in the design.

Requirements
Must have
• photos of my art, a place for my bio, be easy to reach me. tasteful-nothing too "in your face" -my clients are pretty high end and organized. They like clean lines
Nice to have
• sophisticated background, muted tones in the back-similar clean font throughout-no cursive
Should not have
• too many dark areas. Too many blocks of color. Too serious.

```html
<!DOCTYPE html>
<html lang="en">
<head>
<meta charset="utf-8">
<title>Lena Vardell Art</title>
<link rel="stylesheet" href="https://fonts.googleapis.com/css2?family=Playfair+Display:wght@400;500&family=Arimo:wght@400&display=swap">
<style>
:root{
  --cream:#fdf0e1;
  --band:#f2e1ca;
  --accent:#e6554f;
  --ink:#1d1d1d;
  --body:#4a4a4a;
  --footer:#141414;
  --frame:#c9b08e;
  --white:#ffffff;
}
*{margin:0;padding:0;box-sizing:border-box}
html,body{width:1200px;height:3549px;overflow:hidden}
body{position:relative;background:var(--cream);font-family:"Playfair Display",Georgia,serif;color:var(--ink)}
.abs{position:absolute}
.serif{font-family:"Playfair Display",Georgia,serif}
.sans{font-family:"Arimo",Arial,sans-serif}

/* header */
.site-header{left:0;top:0;width:1200px;height:117px;background:var(--cream);border-bottom:1px solid #eadccb}
.brand{left:112px;top:24px;white-space:nowrap}
.brand-name{font-size:33px;letter-spacing:2px;line-height:38px;border-bottom:1px solid var(--ink);padding-bottom:3px;display:block;width:174px}
.brand-sub{font-size:16px;letter-spacing:6.2px;line-height:20px;margin-top:8px}
.nav-item{top:51px;font-size:14px;letter-spacing:.3px;color:var(--ink);white-space:nowrap}
.nav-home{left:503px;top:44px;width:83px;height:35px;border:1px solid var(--accent);border-radius:18px;color:var(--accent);text-align:center;line-height:33px;font-size:14px}
.nav-sep{left:1028px;top:49px;width:1px;height:22px;background:var(--ink)}
.cart-count{left:1080px;top:40px;font-size:10px;color:var(--accent)}

/* hero */
.hero-art{left:0;top:117px;width:1200px;height:723px;
  background:
   radial-gradient(ellipse 420px 260px at 720px 520px,#e8541e 0%,rgba(232,84,30,.6) 35%,rgba(232,84,30,0) 70%),
   radial-gradient(ellipse 300px 260px at 840px 300px,#f2a72c 0%,rgba(242,167,44,0) 70%),
   radial-gradient(ellipse 380px 220px at 160px 600px,#1ea5cf 0%,rgba(30,165,207,0) 75%),
   radial-gradient(ellipse 400px 260px at 1050px 620px,#1a5a9a 0%,rgba(26,90,154,0) 75%),
   linear-gradient(160deg,#bfe8e2 0%,#8fd6cf 45%,#5cc3c6 100%)}
.hero-title{left:112px;top:210px;font-size:68px;line-height:72px;letter-spacing:1px;white-space:nowrap}
.hero-text{left:112px;top:376px;width:470px;font-size:18px;line-height:28px}
.btn-solid{background:var(--accent);color:var(--white);border-radius:30px;text-align:center}
.hero-btn{left:112px;top:452px;width:184px;height:58px;line-height:58px;font-size:19px}
.dot{width:13px;height:13px;border-radius:50%;background:var(--white);left:1124px}

/* paintings */
.section-title{width:1200px;left:0;text-align:center;font-size:55px;letter-spacing:1px}
.v-rule{left:599px;top:969px;width:1px;height:41px;background:var(--accent)}
.art{border:2px solid var(--white);box-shadow:0 3px 6px rgba(0,0,0,.25)}
.card-meta{width:233px;text-align:center}
.product-name{top:1312px;font-size:19px;letter-spacing:.3px}
.btn-outline{border:1px solid var(--ink);border-radius:22px;text-align:center;background:transparent}
.view-btn{top:1352px;width:120px;height:38px;line-height:36px;font-size:12px}
.view-btn.is-active{background:var(--accent);border-color:var(--accent);color:var(--white)}

/* about */
.about-band{left:0;top:1468px;width:1200px;height:627px;background:var(--band)}
.about-rule{left:66px;top:1592px;width:50px;height:1px;background:var(--accent)}
.about-title{left:112px;top:1557px;font-size:55px}
.about-text{left:112px;top:1646px;width:372px;font-size:13.2px;line-height:26.6px;color:var(--body);text-align:justify}
.about-btn{left:112px;top:1936px;width:166px;height:57px;line-height:57px;font-size:18px}

/* gallery */
.gallery-art{border:2px solid var(--frame)}
.gallery-title{left:751px;top:2252px;font-size:52px;white-space:nowrap}
.gallery-rule{left:758px;top:2318px;width:50px;height:1px;background:var(--accent)}
.gallery-text{left:758px;top:2342px;width:325px;font-size:13.2px;line-height:25.7px;color:var(--body)}
.gallery-btn{left:762px;top:2573px;width:149px;height:51px;line-height:49px;font-size:16px;border-color:var(--accent)}

/* contact */
.contact-band{left:0;top:2790px;width:1200px;height:627px;background:var(--band)}
.h-rule{left:575px;top:2921px;width:50px;height:1px;background:var(--accent)}
.field{background:var(--white);border-radius:3px;font-size:11px;padding:18px 0 0 17px;letter-spacing:.3px;color:var(--ink)}
.submit{left:524px;top:3152px;width:153px;height:51px;line-height:51px;font-size:17px}
.info-icon{width:70px;height:70px;border:2px solid var(--accent);border-radius:50%;background:var(--band)}
.info-text{top:3324px;width:300px;text-align:center;font-size:15px;line-height:25px}

/* footer */
.site-footer{left:0;top:3417px;width:1200px;height:132px;background:var(--footer)}
.social{width:34px;height:34px;border:1.5px solid var(--white);border-radius:50%;top:3468px;display:flex;align-items:center;justify-content:center}
.copyright{right:110px;top:3474px;font-size:15px;color:var(--white)}
.copyright .name{color:var(--accent)}
</style>
</head>
<body>

<header class="site-header abs">
  <div class="brand abs">
    <div class="brand-name">LENA</div>
    <div class="brand-sub">VARDELL ART</div>
  </div>
  <div class="nav-home abs">HOME</div>
  <div class="nav-item abs" style="left:610px">ABOUT ME</div>
  <div class="nav-item abs" style="left:728px">PAINTING</div>
  <div class="nav-item abs" style="left:838px">GALLERY</div>
  <div class="nav-item abs" style="left:945px">CONTACT</div>
  <div class="nav-sep abs"></div>
  <svg class="abs" style="left:1044px;top:53px" width="14" height="14" viewBox="0 0 14 14" aria-label="Search"><circle cx="5.8" cy="5.8" r="4.3" fill="none" stroke="#1d1d1d" stroke-width="2"/><line x1="9" y1="9" x2="13" y2="13" stroke="#1d1d1d" stroke-width="2.2"/></svg>
  <div class="cart-count abs">0</div>
  <svg class="abs" style="left:1073px;top:52px" width="16" height="14" viewBox="0 0 16 14" aria-label="Cart"><path d="M0 1h3l2 8h8l2-6H4" fill="none" stroke="#e6554f" stroke-width="2"/><circle cx="6" cy="12" r="1.5" fill="#e6554f"/><circle cx="12" cy="12" r="1.5" fill="#e6554f"/></svg>
</header>

<section>
  <div class="hero-art abs" role="img" aria-label="Abstract oil painting with bold teal, orange and red brush strokes"></div>
  <svg class="abs" style="left:0;top:805px" width="1200" height="36" viewBox="0 0 1200 36" preserveAspectRatio="none"><path d="M0 24 L40 20 L80 27 L130 21 L180 28 L240 22 L300 27 L360 20 L420 26 L480 21 L540 28 L600 22 L660 27 L720 20 L780 26 L840 21 L900 28 L960 22 L1020 27 L1080 21 L1140 26 L1200 22 L1200 36 L0 36Z" fill="#fdf0e1"/></svg>
  <h1 class="hero-title abs serif" style="font-weight:400">LENA<br>VARDELL ART</h1>
  <p class="hero-text abs">Sed ut perspiciatis unde omnis iste natus error sit volupta tem accusantium doloremque laudantium</p>
  <div class="hero-btn btn-solid abs">READ MORE</div>
  <div class="dot abs" style="top:632px"></div>
  <div class="dot abs" style="top:651px;background:var(--accent)"></div>
  <div class="dot abs" style="top:671px"></div>
</section>

<section>
  <h2 class="section-title abs" style="top:895px;font-weight:400">OUR PAINTING</h2>
  <div class="v-rule abs"></div>

  <div class="art abs" style="left:112px;top:1038px;width:233px;height:228px;background:linear-gradient(135deg,#6b4c8e,#cfc3d6 50%,#4e3a6a)" role="img" aria-label="Abstract floral painting in purple and violet"></div>
  <div class="art abs" style="left:360px;top:1038px;width:233px;height:228px;background:linear-gradient(135deg,#2f8a4a,#dde2e0 50%,#2a5a36)" role="img" aria-label="Abstract floral painting in green and black"></div>
  <div class="art abs" style="left:609px;top:1038px;width:233px;height:228px;background:linear-gradient(135deg,#d2a33a,#eef0f3 50%,#3a5a9a)" role="img" aria-label="Abstract rose painting in ochre and blue"></div>
  <div class="art abs" style="left:857px;top:1038px;width:233px;height:228px;background:linear-gradient(135deg,#5a2a22,#e4d4d0 50%,#c08a84)" role="img" aria-label="Abstract rose painting in brown and pink"></div>

  <svg class="abs" style="left:191px;top:1291px" width="75" height="14" viewBox="0 0 75 14"><g fill="#f07a1f"><path id="st" d="M7 0l2 4.5 5 .5-3.8 3.3 1.2 5L7 10.6 2.6 13.3l1.2-5L0 5l5-.5z"/><use href="#st" x="15"/><use href="#st" x="30"/><use href="#st" x="45"/><use href="#st" x="60"/></g></svg>
  <svg class="abs" style="left:439px;top:1291px" width="75" height="14" viewBox="0 0 75 14"><g fill="#f07a1f"><use href="#st"/><use href="#st" x="15"/><use href="#st" x="30"/><use href="#st" x="45"/><use href="#st" x="60"/></g></svg>
  <svg class="abs" style="left:688px;top:1291px" width="75" height="14" viewBox="0 0 75 14"><g fill="#f07a1f"><use href="#st"/><use href="#st" x="15"/><use href="#st" x="30"/><use href="#st" x="45"/><use href="#st" x="60"/></g></svg>
  <svg class="abs" style="left:936px;top:1291px" width="75" height="14" viewBox="0 0 75 14"><g fill="#f07a1f"><use href="#st"/><use href="#st" x="15"/><use href="#st" x="30"/><use href="#st" x="45"/><use href="#st" x="60"/></g></svg>

  <div class="card-meta product-name abs" style="left:112px">PRODUCT NAME</div>
  <div class="card-meta product-name abs" style="left:360px">PRODUCT NAME</div>
  <div class="card-meta product-name abs" style="left:609px">PRODUCT NAME</div>
  <div class="card-meta product-name abs" style="left:857px">PRODUCT NAME</div>

  <div class="btn-outline view-btn abs" style="left:167px">VIEW DETAILS</div>
  <div class="btn-outline view-btn is-active abs" style="left:416px">VIEW DETAILS</div>
  <div class="btn-outline view-btn abs" style="left:664px">VIEW DETAILS</div>
  <div class="btn-outline view-btn abs" style="left:913px">VIEW DETAILS</div>
</section>

<section>
  <div class="about-band abs"></div>
  <svg class="abs" style="left:0;top:1460px" width="1200" height="16" viewBox="0 0 1200 16" preserveAspectRatio="none"><path d="M0 10 L60 6 L120 11 L190 5 L260 10 L330 6 L400 12 L470 6 L540 10 L610 5 L680 11 L750 6 L820 10 L890 5 L960 11 L1030 6 L1100 10 L1200 6 L1200 16 L0 16Z" fill="#f2e1ca"/></svg>
  <svg class="abs" style="left:0;top:2089px" width="1200" height="16" viewBox="0 0 1200 16" preserveAspectRatio="none"><path d="M0 0 L1200 0 L1200 6 L1120 10 L1040 5 L960 11 L880 6 L800 10 L720 5 L640 11 L560 6 L480 10 L400 5 L320 11 L240 6 L160 10 L80 5 L0 9Z" fill="#f2e1ca"/></svg>
  <div class="about-rule abs"></div>
  <h2 class="about-title abs" style="font-weight:400">ABOUT ME</h2>
  <p class="about-text abs sans">Sed ut perspiciatis unde omnis iste natus error sit voluptatem accusantium doloremque laudantium, totam rem aperiam, eaque ipsa quae ab illo inventore veritatis et quasi architecto beatae vitae dicta sunt explicabo. Nemo enim ipsam volupt atem quia voluptas sit aspernatur aut odit aut fugit, sed quia consequuntur magni dolores eos qui ratione voluptatem sequi nesciunt. Neque porro quisquam est, qui dolorem ipsum quia dolor sit amet, consectetur, adipisci velit, sed quia non numq uam eius modi tempora incidunt ut labore et dolore magnam unde omnis aliquam quaerat voluptatem</p>
  <div class="about-btn btn-solid abs">READ MORE</div>

  <div class="abs" style="left:540px;top:1560px;width:560px;height:470px;border-radius:50%;background:radial-gradient(ellipse at 30% 45%,rgba(228,120,190,.45),rgba(228,120,190,0) 55%),radial-gradient(ellipse at 78% 60%,rgba(240,200,90,.45),rgba(240,200,90,0) 50%)" role="img" aria-label="Soft pink and yellow paint splash decoration"></div>
  <div class="abs" style="left:602px;top:1573px;width:446px;height:446px;border-radius:50%;background:#d3bc98"></div>
  <div class="abs" style="left:611px;top:1582px;width:428px;height:428px;border-radius:50%;background:var(--white)"></div>
  <div class="abs" style="left:621px;top:1592px;width:408px;height:408px;border-radius:50%;background:linear-gradient(120deg,#c9dbe6 0%,#eef1f3 40%,#9aa6c2 75%,#c6763e 100%)" role="img" aria-label="Portrait photo of the artist at her easel"></div>
</section>

<section>
  <div class="gallery-art abs" style="left:113px;top:2227px;width:187px;height:251px;background:linear-gradient(135deg,#6b4c8e,#cfc3d6 50%,#4e3a6a)" role="img" aria-label="Abstract floral painting in purple"></div>
  <div class="gallery-art abs" style="left:113px;top:2492px;width:187px;height:250px;background:linear-gradient(180deg,#e9e6e0 0%,#e9e6e0 30%,#4a9cc4 45%,#dfe6ea 100%)" role="img" aria-label="Abstract drip painting in blue and white"></div>
  <div class="gallery-art abs" style="left:314px;top:2177px;width:188px;height:251px;background:linear-gradient(90deg,#8a93a8 0%,#a7adbd 30%,#e8dcc6 45%,#f0e7d6 60%,#0f7a6c 65%,#0f7a6c 100%)" role="img" aria-label="Abstract painting with grey, cream and teal vertical bands"></div>
  <div class="gallery-art abs" style="left:314px;top:2443px;width:188px;height:251px;background:linear-gradient(135deg,#2f8a4a,#dde2e0 50%,#2a5a36)" role="img" aria-label="Abstract floral painting in green"></div>
  <div class="gallery-art abs" style="left:515px;top:2224px;width:188px;height:252px;background:linear-gradient(135deg,#d2a33a,#eef0f3 50%,#3a5a9a)" role="img" aria-label="Abstract rose painting in ochre and blue"></div>
  <div class="gallery-art abs" style="left:515px;top:2492px;width:116px;height:151px;background:linear-gradient(135deg,#5a2a22,#e4d4d0 50%,#c08a84)" role="img" aria-label="Abstract rose painting in brown and pink"></div>

  <h2 class="gallery-title abs" style="font-weight:400">OUR GALLERY</h2>
  <div class="gallery-rule abs"></div>
  <p class="gallery-text abs sans">Sed ut perspiciatis unde omnis iste natus error sit vol uptatem accusantium doloremque laudantium, totam rem aperiam, eaque ipsa quae ab illo inventore verit atis et quasi architecto beatae vitae dicta sunt explic abo. Nemo enim ipsam voluptatem quia voluptas sit aspernatur aut odit aut fugit, sed quia consequuntur magni dolores eos qui ratione voluptatem sequi unde iste omnis iste natus nesciunt</p>
  <div class="btn-outline gallery-btn abs">READ MORE</div>
</section>

<section>
  <div class="contact-band abs"></div>
  <svg class="abs" style="left:0;top:2782px" width="1200" height="16" viewBox="0 0 1200 16" preserveAspectRatio="none"><path d="M0 9 L70 5 L140 11 L210 6 L280 10 L350 5 L420 11 L490 6 L560 10 L630 5 L700 11 L770 6 L840 10 L910 5 L980 11 L1050 6 L1120 10 L1200 6 L1200 16 L0 16Z" fill="#f2e1ca"/></svg>
  <h2 class="section-title abs" style="top:2845px;font-weight:400">CONTACT US</h2>
  <div class="h-rule abs"></div>
  <div class="field abs" style="left:298px;top:2953px;width:295px;height:46px">FIRST NAME :</div>
  <div class="field abs" style="left:608px;top:2953px;width:295px;height:46px">LAST NAME :</div>
  <div class="field abs" style="left:298px;top:3008px;width:295px;height:46px">EMAIL :</div>
  <div class="field abs" style="left:608px;top:3008px;width:295px;height:46px">PHONE :</div>
  <div class="field abs" style="left:298px;top:3062px;width:605px;height:72px">MESSAGE :</div>
  <div class="submit btn-solid abs">SUBMIT</div>

  <div class="info-icon abs" style="left:323px;top:3243px"></div>
  <svg class="abs" style="left:349px;top:3265px" width="18" height="25" viewBox="0 0 18 25" aria-label="Location"><path d="M9 0a9 9 0 0 1 9 9c0 6-9 16-9 16S0 15 0 9a9 9 0 0 1 9-9z" fill="#e6554f"/><circle cx="9" cy="9" r="3.5" fill="#f2e1ca"/></svg>
  <div class="info-icon abs" style="left:569px;top:3243px"></div>
  <svg class="abs" style="left:594px;top:3268px" width="20" height="20" viewBox="0 0 20 20" aria-label="Phone"><path d="M4 1l4 4-2.5 2.5a12 12 0 0 0 7 7L15 12l4 4-3 3C8 19 1 12 1 4z" fill="#e6554f"/></svg>
  <div class="info-icon abs" style="left:826px;top:3243px"></div>
  <svg class="abs" style="left:850px;top:3270px" width="22" height="16" viewBox="0 0 22 16" aria-label="Email"><rect width="22" height="16" rx="2" fill="#e6554f"/><path d="M1 2l10 7 10-7" fill="none" stroke="#f2e1ca" stroke-width="1.6"/></svg>

  <div class="info-text abs" style="left:208px">P O Box Lorem Ipsum Dummy<br>Lorem 2163</div>
  <div class="info-text abs" style="left:454px">+1 888 888 8888</div>
  <div class="info-text abs" style="left:711px">info@lenavardellart.com</div>
</section>

<footer class="site-footer abs">
  <svg class="abs" style="left:0;top:-8px" width="1200" height="16" viewBox="0 0 1200 16" preserveAspectRatio="none"><path d="M0 8 L50 3 L100 9 L160 4 L220 10 L290 4 L350 9 L420 3 L490 10 L560 4 L630 9 L700 3 L770 10 L840 4 L910 9 L980 3 L1050 10 L1120 4 L1200 8 L1200 16 L0 16Z" fill="#141414"/></svg>
</footer>
<div class="social abs" style="left:113px" aria-label="Email link"><svg width="16" height="12" viewBox="0 0 16 12"><rect x="1" y="1" width="14" height="10" rx="1" fill="none" stroke="#fff" stroke-width="1.4"/><path d="M1.5 1.5l6.5 5 6.5-5" fill="none" stroke="#fff" stroke-width="1.4"/></svg></div>
<div class="social abs" style="left:156px" aria-label="Website link"><svg width="16" height="16" viewBox="0 0 16 16"><circle cx="8" cy="8" r="6.5" fill="none" stroke="#fff" stroke-width="1.4"/><path d="M1.5 8h13M8 1.5c-3 3.5-3 9.5 0 13M8 1.5c3 3.5 3 9.5 0 13" fill="none" stroke="#fff" stroke-width="1.2"/></svg></div>
<div class="social abs" style="left:199px" aria-label="Location link"><svg width="12" height="16" viewBox="0 0 12 16"><path d="M6 .5a5.5 5.5 0 0 1 5.5 5.5C11.5 10 6 15.5 6 15.5S.5 10 .5 6A5.5 5.5 0 0 1 6 .5z" fill="#fff"/><circle cx="6" cy="6" r="2" fill="#141414"/></svg></div>
<div class="social abs" style="left:242px" aria-label="Phone link"><svg width="14" height="14" viewBox="0 0 20 20"><path d="M4 1l4 4-2.5 2.5a12 12 0 0 0 7 7L15 12l4 4-3 3C8 19 1 12 1 4z" fill="#fff"/></svg></div>
<div class="social abs" style="left:285px" aria-label="Favourite link"><svg width="15" height="14" viewBox="0 0 16 14"><path d="M8 13.5S1 9 1 4.5A3.5 3.5 0 0 1 8 3a3.5 3.5 0 0 1 7 1.5C15 9 8 13.5 8 13.5z" fill="#fff"/></svg></div>
<div class="copyright abs">© Copyright 2022 <span class="name">Lena Vardell Art</span>.All Rights Reserved</div>

</body>
</html>
```